Business Card Design

I need a business card design for my new business based on Long Island, NY also serving NYC called Pawhaven Retreat. I have built a website with cardmint that can be looked at as a basis for the card. It is pawhavenretreat.com.

I board Labrador Retrievers in my home. Specialize in one breed. Cage free environment. Dogs have full run of home and fenced in property. Pawhaven Retreat is a one-of-a-kind, high-quality dog-boarding provider serving specifically Labrador Retrievers. By working with a dog I am comfortable with, I am able to offer the best care for all pets that come through my door. I work with Lab owners in the Long Island/NYC area to provide an
in-home safe, reliable and fun environment for daycare and overnight stays.

I provide a unique boarding experience for Labrador Retrievers on Long Island. Your Lab should be well mannered, housebroken and good with other dogs. Provided your pet is well mannered and house trained, my boarding services allow dogs to experience a cage-free stay while having free roam of my home and property. This allows owners a unique alternative to a kennel, giving pets the chance to experience a home away from home rather than chain linked fences and cold concrete floors.
As a guest at Pawhaven Retreat, your dog will get:

4-star kibble
Access to my in-ground pool
All-natural snack selection
Companionship of other retrievers including my two
Full run of entire home and fenced-in backyard
Photos AND videos posted to Snapgram so you can see your dog having fun while away
Toys, bones and affection

I think it is important to have a pic of the 3 colored labs below. Also the picture of my own personal labs ..the white one with the black puppy. Maybe some paw prints. If using any imagery that MUST look EXACTLY like labrador retriever no generic dogs. Thank you
Updates

The Back of the Card should have the following: The background should be one of the pictures I sent (white dog in pool or another pic I included) At Pawhaven Retreat your Lab gets: Cage Free Environment Full run of my home and fenced in yard In-ground pool Toys and affection Companionship of other Labrador Retrievers Photos and Videos posted Snapgram of your loved one FRONT OF THE CARD: should include picture of the 3 labs (yellow white brown) OR picture of white dog in pool. Pawhaven Retreat should be in larger font than the rest. the following can be in any order. Tom Pelley Linden Bay in Central Long Island pawhavenretreat.com 631-555-0192

Industry/Entity Type

Environment

Contact Information for Business Card

Pawhaven Retreat
Linden Bay
Tom Pelley
hello@pawhavenretreat.com
631-555-0192

```html
<!DOCTYPE html>
<html lang="en">
<head>
<meta charset="utf-8">
<title>Pawhaven Retreat – Business Card</title>
<link rel="stylesheet" href="https://fonts.googleapis.com/css2?family=Roboto:wght@300;400&display=swap">
<style>
  :root {
    --page: #e9e6e2;
    --card: #ffffff;
    --ink: #111111;
    --panel: #000000;
    --accent: #e3a15b;
    --rule: #222222;
    --photo-light: #e6c89a;
    --photo-mid: #b98a55;
    --photo-dark: #3b2a1c;
  }
  * { box-sizing: border-box; margin: 0; padding: 0; }
  html, body {
    width: 1200px; height: 914px; overflow: hidden;
    background: var(--page);
    font-family: "Roboto", Arial, sans-serif;
    font-weight: 300;
    color: var(--ink);
  }
  .sheet {
    width: 1200px; height: 914px;
    display: flex; flex-direction: column;
    align-items: center; justify-content: center; gap: 30px;
  }
  .card {
    position: relative;
    width: 720px; height: 412px;
    background: var(--card);
    overflow: hidden;
    box-shadow: 0 4px 14px rgba(0,0,0,0.15);
  }

  /* front */
  .photo-panel {
    position: absolute; left: 0; top: 14px;
    width: 332px; height: 362px;
    background: var(--panel);
    border-radius: 0 44px 70px 0;
  }
  .photo-panel .dogs {
    position: absolute; left: 24px; top: 60px;
    width: 280px; height: 240px;
    border-radius: 40% 40% 30% 30%;
    background: radial-gradient(ellipse at 60% 60%, var(--photo-light) 0%, var(--photo-mid) 45%, var(--photo-dark) 75%, var(--panel) 100%);
  }
  .edge-tab {
    position: absolute; top: 36px; bottom: 40px; width: 30px;
    background: var(--panel);
  }
  .edge-tab.right { right: 0; border-radius: 30px 0 0 30px; }
  .edge-tab.left { left: 0; border-radius: 0 30px 30px 0; }

  .identity {
    position: absolute; left: 368px; top: 96px; width: 320px;
  }
  .business-name { font-size: 31px; font-weight: 300; letter-spacing: 0.5px; line-height: 1.2; white-space: nowrap; }
  .owner-line { font-size: 25px; margin-top: 14px; line-height: 1.2; white-space: nowrap; }
  .divider { height: 1px; background: var(--rule); margin: 40px 0 0 -20px; width: 300px; }

  .contact { position: absolute; left: 360px; top: 290px; list-style: none; }
  .contact li { display: flex; align-items: center; gap: 14px; font-size: 20px; line-height: 1.4; }
  .contact svg { width: 16px; height: 16px; flex: none; }
  .contact .icon-phone { fill: var(--accent); }
  .contact .icon-mail { fill: none; stroke: var(--accent); stroke-width: 2; }

  /* back */
  .perks {
    position: absolute; left: 60px; right: 60px; top: 60px;
    text-align: center;
  }
  .perks h2 { font-size: 24px; font-weight: 300; margin-bottom: 34px; }
  .perks ul { list-style: none; font-size: 17px; line-height: 1.32; }
</style>
</head>
<body>
<main class="sheet">
  <section class="card card-front">
    <div class="photo-panel">
      <div class="dogs" role="img" aria-label="Photo of three Labrador retriever puppies lying together on black"></div>
    </div>
    <div class="edge-tab right"></div>
    <div class="identity">
      <h1 class="business-name">Pawhaven Retreat</h1>
      <p class="owner-line">Linden Bay &nbsp;Tom Pelley</p>
      <div class="divider"></div>
    </div>
    <ul class="contact">
      <li>
        <svg class="icon-phone" viewBox="0 0 24 24" aria-hidden="true"><path d="M6.6 10.8a15.1 15.1 0 0 0 6.6 6.6l2.2-2.2a1 1 0 0 1 1-.25 11.4 11.4 0 0 0 3.6.57 1 1 0 0 1 1 1V20a1 1 0 0 1-1 1A17 17 0 0 1 3 4a1 1 0 0 1 1-1h3.5a1 1 0 0 1 1 1c0 1.25.2 2.45.57 3.6a1 1 0 0 1-.25 1z"/></svg>
        631-555-0192
      </li>
      <li>
        <svg class="icon-mail" viewBox="0 0 24 24" aria-hidden="true"><rect x="2" y="5" width="20" height="14"/><path d="M2 5l10 8 10-8"/></svg>
        hello@pawhavenretreat.com
      </li>
    </ul>
  </section>

  <section class="card card-back">
    <div class="edge-tab left"></div>
    <div class="edge-tab right"></div>
    <div class="perks">
      <h2>As a guest at Pawhaven Retreat, your dog will get</h2>
      <ul>
        <li>4-star kibble</li>
        <li>Access to my in-ground pool</li>
        <li>All-natural snack selection</li>
        <li>Companionship of other retrievers including my two</li>
        <li>Full run of entire home and fenced-in backyard</li>
        <li>Photos AND videos posted to Snapgram so you can see<br>your dog having fun while away</li>
        <li>Toys, bones and affection</li>
      </ul>
    </div>
  </section>
</main>
</body>
</html>
```